Request for Business Card Design

Hi. My name is Marlene, I am looking for a new business card design for my company, Quarrow Signal Instruments, LLC. I really like the design you did for Tarsel Venture and was hoping you could do something similar using our full logo and our mark. I am also open to any raised texture design using our mark. I have attached our full logo, which would need to be somewhere on the card, as well as the mark in both outline and full form, as well as our brand colors / guide. The card does not have to be white, as long as our logo and mark appear. I actually like darker colored business cards more, but am open to all options. If you are interested in working with me, please let me know. We would also take the business card design into letterhead design if you can do that.

```html
<!DOCTYPE html>
<html lang="en">
<head>
<meta charset="UTF-8">
<title>Quarrow Signal Instruments — Business Card</title>
<link href="https://fonts.googleapis.com/css2?family=Barlow:wght@400;500;600;700&display=swap" rel="stylesheet">
<style>
  :root {
    --bg-light: #e4e4e4;
    --bg-dark: #9a9a9a;
    --card-dark: #434345;
    --card-dark-hi: #5a5a5c;
    --card-light: #f1f1f1;
    --ink: #3a3a3c;
    --ink-soft: #444446;
    --brand-blue: #2f9cc0;
    --white: #ffffff;
  }
  * { box-sizing: border-box; margin: 0; padding: 0; }
  html, body { width: 1200px; height: 1200px; overflow: hidden; }
  body {
    background: linear-gradient(135deg, var(--bg-light) 0%, #c8c8c8 45%, var(--bg-dark) 100%);
    font-family: "Barlow", Arial, sans-serif;
    position: relative;
  }
  .card {
    position: absolute;
    left: 250px;
    width: 700px;
    height: 400px;
    border-radius: 22px;
    box-shadow: 0 14px 30px rgba(0,0,0,0.25);
  }
  .card--front {
    top: 140px;
    background: linear-gradient(120deg, var(--card-dark-hi) 0%, var(--card-dark) 55%, #3d3d3f 100%);
  }
  .card--back {
    top: 640px;
    background: var(--card-light);
  }
  .brand {
    position: absolute;
    display: flex;
    align-items: center;
    gap: 24px;
  }
  .brand__dot {
    width: 70px; height: 70px;
    border-radius: 50%;
    background: var(--brand-blue);
    flex: none;
  }
  .brand__name {
    font-weight: 700;
    letter-spacing: 3px;
    line-height: 1.05;
    text-transform: uppercase;
  }
  .card--front .brand { left: 110px; top: 155px; }
  .card--front .brand__name { color: var(--white); font-size: 40px; }
  .card--back .brand { left: 110px; top: 48px; }
  .card--back .brand__name { color: var(--ink); font-size: 40px; }
  .brand__dot--small { width: 62px; height: 62px; }

  .person {
    position: absolute;
    top: 160px;
    width: 100%;
    text-align: center;
  }
  .person__name { color: var(--brand-blue); font-weight: 700; font-size: 30px; }
  .person__title { color: var(--ink-soft); font-size: 19px; letter-spacing: 1px; margin-top: 2px; }
  .rule {
    position: absolute;
    left: 60px; right: 60px;
    top: 248px;
    height: 2px;
    background: var(--brand-blue);
  }
  .contacts {
    position: absolute;
    left: 60px; top: 266px;
    list-style: none;
  }
  .contacts li {
    display: flex; align-items: center; gap: 12px;
    font-size: 19px; color: var(--ink-soft);
    letter-spacing: 0.8px; line-height: 27px;
  }
  .contacts svg { width: 18px; height: 18px; fill: var(--brand-blue); flex: none; }
  .address {
    position: absolute;
    right: 60px; top: 266px;
    text-align: right;
    font-size: 19px; color: var(--ink-soft);
    letter-spacing: 0.8px; line-height: 27px;
    font-style: normal;
  }
</style>
</head>
<body>
  <section class="card card--front">
    <div class="brand">
      <span class="brand__dot"></span>
      <div class="brand__name">Quarrow<br>Signal Instruments</div>
    </div>
  </section>

  <section class="card card--back">
    <div class="brand">
      <span class="brand__dot brand__dot--small"></span>
      <div class="brand__name">Quarrow<br>Signal Instruments</div>
    </div>

    <div class="person">
      <div class="person__name">Marlene</div>
      <div class="person__title">Founder &amp; Director</div>
    </div>

    <div class="rule"></div>

    <ul class="contacts">
      <li>
        <svg viewBox="0 0 24 24" aria-hidden="true"><path d="M6.6 10.8a15 15 0 0 0 6.6 6.6l2.2-2.2c.3-.3.7-.4 1-.2 1.1.4 2.3.6 3.6.6.6 0 1 .4 1 1V20c0 .6-.4 1-1 1A17 17 0 0 1 3 4c0-.6.4-1 1-1h3.5c.6 0 1 .4 1 1 0 1.3.2 2.5.6 3.6.1.3 0 .7-.2 1z"/></svg>
        +001 555 210 4837
      </li>
      <li>
        <svg viewBox="0 0 24 24" aria-hidden="true"><path d="M6 2h12v5H6zM4 8h16a2 2 0 0 1 2 2v7h-4v5H6v-5H2v-7a2 2 0 0 1 2-2zm4 8v4h8v-4z"/></svg>
        +001 555 210 4890
      </li>
      <li>
        <svg viewBox="0 0 24 24" aria-hidden="true"><path d="M2 5h20v14H2zm2 2v.5l8 5 8-5V7z"/></svg>
        info@quarrowsignal.com
      </li>
      <li>
        <svg viewBox="0 0 24 24" aria-hidden="true"><path d="M12 2a10 10 0 1 0 0 20 10 10 0 0 0 0-20zm0 2c.9 1.2 1.6 2.9 1.9 5h-3.8c.3-2.1 1-3.8 1.9-5zM4.3 11h3.8c0 .7 0 1.4.1 2H4.3a8 8 0 0 1 0-2zm5.8 0h3.8v2h-3.8v-2zm5.8 0h3.8a8 8 0 0 1 0 2h-3.9c.1-.6.1-1.3.1-2zM12 20c-.9-1.2-1.6-2.9-1.9-5h3.8c-.3 2.1-1 3.8-1.9 5z"/></svg>
        www.quarrowsignal.com
      </li>
    </ul>

    <address class="address">
      1180 Meridian Works Road.<br>
      Halden Falls,<br>
      CO 80612
    </address>
  </section>
</body>
</html>
```